Bespoke Branding Agency "Tidal Crest" seeks uplifting wordpress site

Looking for a SIMPLE, CLEAN, easy to manage wordpress site for our start-up Branding business. Our company is "Tidal Crest" and the site should reflect our vision.

We formed the company after making the decision never to work the average 9 to 5 work life again. We have vowed to never work in traditional corporate culture again. We are committed to a happier life with reduced stress and increased job satisfaction.

We want to build brands that make people happy.

We want to work with people who believe that you don’t have to be an asshole to be successful.

We believe that success should not be measured in monetary terms, but rather in happiness scores.

We believe in the Corwin Ashdale song lyric "Rivers bend toward evening”.

We love sunflowers.

We prefer brevity over long wind.

We are motivated by creativity not money.

We love spending time with friends and family, and see this as our main priority in life.

We know life is short.

```html
<!DOCTYPE html>
<html lang="en">
<head>
<meta charset="utf-8">
<title>Tidal Crest — Company</title>
<link rel="stylesheet" href="https://fonts.googleapis.com/css2?family=Open+Sans:wght@300;400&family=Arimo:wght@400;700&display=swap">
<style>
  :root {
    --teal: #00b2c5;
    --green: #7dc566;
    --white: #ffffff;
    --heading-font: "Open Sans", sans-serif;
    --body-font: "Arimo", Arial, sans-serif;
  }
  * { margin: 0; padding: 0; box-sizing: border-box; }
  html, body { width: 1200px; height: 900px; overflow: hidden; }
  body { position: relative; font-family: var(--body-font); color: var(--white); background: var(--white); }

  .section { position: absolute; left: 0; width: 1200px; }
  .company { top: 0; height: 720px; background: var(--teal); }
  .services { top: 721px; height: 179px; background: var(--green); overflow: hidden; }
  .divider-line { position: absolute; left: 0; top: 720px; width: 1200px; height: 1px; background: #e8f6f7; }
  .notch { position: absolute; left: 532px; width: 134px; height: 58px; }
  .notch-top { top: 0; }
  .notch-services { top: 0; }

  .section-title {
    position: absolute; left: 0; width: 100%; text-align: center;
    font-family: var(--heading-font); font-weight: 400; font-size: 88px; letter-spacing: 1px; line-height: 1;
  }
  .company .section-title { top: 88px; left: -10px; }
  .services .section-title { top: 114px; }

  .intro {
    position: absolute; left: 62px; top: 216px; width: 1080px;
    font-size: 16px; line-height: 25.6px;
  }

  .column-title {
    position: absolute; font-family: var(--body-font); font-weight: 400; font-size: 27px; text-align: center; width: 300px;
  }
  .why-title { left: 68px; top: 388px; }
  .values-title { left: 439px; top: 387px; }

  .why-list { position: absolute; left: 76px; top: 450px; list-style: none; }
  .why-list li { position: relative; height: 54px; padding-left: 30px; font-size: 13px; line-height: 24px; }
  .why-list li::after {
    content: ""; position: absolute; left: 29px; top: 38px; width: 270px; height: 1px; background: var(--white);
  }
  .why-list svg { position: absolute; left: 0; top: 5px; }

  .values-text { position: absolute; left: 465px; top: 449px; width: 292px; font-size: 13px; line-height: 23.5px; }

  .stat-figure { position: absolute; font-size: 64px; line-height: 1; font-weight: 400; }
  .stat-label { position: absolute; font-size: 27px; line-height: 1; }
  .clients-figure { left: 851px; top: 405px; }
  .clients-label { left: 863px; top: 476px; }
  .solutions-figure { left: 853px; top: 542px; }
  .solutions-label { left: 856px; top: 612px; }
</style>
</head>
<body>
  <section class="section company">
    <svg class="notch notch-top" viewBox="0 0 134 58" aria-hidden="true"><polygon points="0,0 134,0 67,58" fill="var(--white)"/></svg>
    <h1 class="section-title">COMPANY</h1>
    <p class="intro">Lorem Ipsum is simply dummy text of the printing and typesetting industry. Lorem Ipsum has been the industry's standard dummy text ever since the 1500s, when an unknown printer took a galley of type and scrambled it to make a type specimen book. It has survived not only five centuries, but also the leap into electronic typesetting, remaining essentially unchanged. It was popularised in the 1960s with the release of Marlowe Press sheets containing Lorem Ipsum passages, and more recently with desktop publishing software like Quillset Layout including versions of Lorem Ipsum.</p>

    <h2 class="column-title why-title">Why we</h2>
    <ul class="why-list">
      <li><svg width="15" height="15" viewBox="0 0 15 15" aria-hidden="true"><circle cx="7.5" cy="7.5" r="7" fill="var(--white)"/><path d="M7.5 3.5v8M3.5 7.5h8" stroke="var(--teal)" stroke-width="2"/></svg>Maker including versions of Lorem Ipsum.</li>
      <li><svg width="15" height="15" viewBox="0 0 15 15" aria-hidden="true"><circle cx="7.5" cy="7.5" r="7" fill="var(--white)"/><path d="M7.5 3.5v8M3.5 7.5h8" stroke="var(--teal)" stroke-width="2"/></svg>Maker including versions of Lorem Ipsum.</li>
      <li><svg width="15" height="15" viewBox="0 0 15 15" aria-hidden="true"><circle cx="7.5" cy="7.5" r="7" fill="var(--white)"/><path d="M7.5 3.5v8M3.5 7.5h8" stroke="var(--teal)" stroke-width="2"/></svg>Maker including versions of Lorem Ipsum.</li>
      <li><svg width="15" height="15" viewBox="0 0 15 15" aria-hidden="true"><circle cx="7.5" cy="7.5" r="7" fill="var(--white)"/><path d="M7.5 3.5v8M3.5 7.5h8" stroke="var(--teal)" stroke-width="2"/></svg>Maker including versions of Lorem Ipsum.</li>
    </ul>

    <h2 class="column-title values-title">Our Values</h2>
    <p class="values-text">Lorem Ipsum has been the industry's stan-dard dummy text ever since the 1500s, when an unknown printer took a galley of type and scrambled it to make a type specimen book. It has survived not only five centuries, but also the leap into electronic typesetting, remaining essentially unchanged.</p>

    <div class="stat-figure clients-figure">16,000 +</div>
    <div class="stat-label clients-label">Happy Clients</div>
    <div class="stat-figure solutions-figure">100 %</div>
    <div class="stat-label solutions-label">Practical Solutions</div>
  </section>

  <div class="divider-line"></div>

  <section class="section services">
    <svg class="notch notch-services" viewBox="0 0 134 58" aria-hidden="true"><polygon points="0,0 134,0 67,58" fill="var(--white)"/></svg>
    <h2 class="section-title">SERVICES</h2>
  </section>
</body>
</html>
```